Wine Label for Tavelora Vineyards

I grow my own grapes and make my own wine. I do this just as a hobby and do not sell any wine. I just make it for my own use and to give as gifts. I still endeavor to make the bottle look like a genuine retail bottle, so I need a professional looking label.

Quenby Knob is a state park in North Carolina. My vineyard is at the base of the mountain. Tavelora is the name the Indians called the mountain. It means "great guide" as they used the mountain as a landmark in their travels.

Need front and back label. Attached is a picture that I currently use. The new labels should contain all the language on the current label.

Size of label flexible as long as it is a standard size label, that can be easily found.

I think Quenby Knob image should be included, maybe stylized. I am looking for something for earthy, rustic and clean.

The varieties will be Pinot Noir, Cabernet Sauvignon, Carbernet Franc, Chardonnay, and Viognier. I guess all the labels would be the same, just the name would change, Unless someone has a better idea.

Target Market(s)

wine drinker

Requirements
Must have
• quenby knob image of some sort,
• front and back label
Nice to have
• Clean, earthy, rustic - the label should feel like the mountain look, even romantic

```html
<!DOCTYPE html>
<html lang="en">
<head>
<meta charset="utf-8">
<title>Tavelora Vineyards – Cabernet Sauvignon Label</title>
<link href="https://fonts.googleapis.com/css2?family=Cinzel:wght@400;500&family=Cormorant+Garamond:wght@400;500&family=Pinyon+Script&display=swap" rel="stylesheet">
<style>
  :root {
    --page-bg: #2b2826;
    --label-light: #f4f4f3;
    --label-mid: #e2e2e0;
    --label-edge: #cfcfcc;
    --ink: #2a2624;
    --ink-soft: #4a4542;
    --gold: #c79a2c;
    --gold-light: #e6c35c;
    --gold-dark: #8d6a17;
    --sketch-light: #e6e6e4;
    --sketch-mid: #b9b8b5;
    --sketch-dark: #8a8884;
  }
  * { margin: 0; padding: 0; box-sizing: border-box; }
  html, body {
    width: 1200px; height: 1200px; overflow: hidden;
    background: var(--page-bg);
  }
  .canvas { position: relative; width: 1200px; height: 1200px; }

  .label {
    position: absolute; left: 270px; top: 80px;
    width: 660px; height: 1040px;
    background: linear-gradient(90deg, var(--label-edge) 0%, var(--label-mid) 8%, var(--label-light) 35%, var(--label-light) 60%, var(--label-mid) 90%, var(--label-edge) 100%);
    color: var(--ink);
    text-align: center;
  }
  .gold-rule {
    position: absolute; left: 0; width: 100%; height: 5px;
    background: linear-gradient(90deg, var(--gold-dark), var(--gold-light), var(--gold), var(--gold-light), var(--gold-dark));
  }
  .gold-rule.top { top: 4px; }
  .gold-rule.bottom { bottom: 4px; }

  .brand {
    position: absolute; top: 52px; left: 0; width: 100%;
    font-family: "Cinzel", serif; font-weight: 500;
    font-size: 70px; letter-spacing: 8px; line-height: 1;
  }
  .brand-sub {
    position: absolute; top: 163px; left: 0; width: 100%;
    font-family: "Cinzel", serif; font-size: 30px; letter-spacing: 5px; line-height: 1;
    color: var(--ink-soft);
  }
  .varietal {
    position: absolute; top: 250px; left: 0; width: 100%;
    font-family: "Pinyon Script", cursive; font-size: 62px; line-height: 1;
    color: var(--ink-soft);
  }
  .year-caption {
    position: absolute; top: 370px; left: 0; width: 100%;
    display: flex; justify-content: center; align-items: center; gap: 22px;
    font-family: "Cormorant Garamond", serif; font-size: 16px; letter-spacing: 3px;
  }
  .year-caption .dash { width: 52px; height: 2px; background: var(--ink); }
  .vintage {
    position: absolute; top: 398px; left: 0; width: 100%;
    font-family: "Cormorant Garamond", serif; font-weight: 500; font-size: 76px; line-height: 1;
  }
  .origin-band {
    position: absolute; top: 495px; left: 0; width: 100%; height: 34px;
    background: linear-gradient(180deg, var(--gold-light), var(--gold) 50%, var(--gold-dark));
    font-family: "Cormorant Garamond", serif; font-variant: small-caps;
    font-size: 21px; line-height: 34px; color: #2e2208; letter-spacing: 1px;
  }
  .volume {
    position: absolute; top: 570px; left: 0; width: 100%;
    font-family: "Cormorant Garamond", serif; font-size: 21px; letter-spacing: 1.5px;
  }
  .producer-note {
    position: absolute; top: 612px; left: 0; width: 100%;
    font-family: "Cormorant Garamond", serif; font-size: 15px; line-height: 17px;
    color: var(--ink-soft);
  }
  .knob-art {
    position: absolute; top: 705px; left: 15px; width: 630px; height: 315px;
  }
</style>
</head>
<body>
<div class="canvas">
  <section class="label">
    <div class="gold-rule top"></div>

    <h1 class="brand">TAVELORA</h1>
    <p class="brand-sub">VINEYARDS</p>
    <p class="varietal">Cabernet Sauvignon</p>

    <div class="year-caption"><span class="dash"></span><span>YEAR</span><span class="dash"></span></div>
    <p class="vintage">2015</p>

    <div class="origin-band">Product of USA - North Carolina</div>

    <p class="volume">ALC. 13.5% BY VOL · 750 ML</p>
    <p class="producer-note">
      Fermented &amp; bottled by:<br>
      Company name. LTD<br>
      Yadkin Valley Appellation,<br>
      North Carolina<br>
      Contains Sulfites
    </p>

    <svg class="knob-art" viewBox="0 0 630 315" role="img" aria-label="Pencil sketch of Quenby Knob rising above farmhouses and rows of vineyard vines">
      <defs>
        <radialGradient id="sketchTone" cx="50%" cy="45%" r="60%">
          <stop offset="0%" stop-color="var(--sketch-mid)"/>
          <stop offset="60%" stop-color="var(--sketch-light)"/>
          <stop offset="100%" stop-color="var(--label-light)" stop-opacity="0"/>
        </radialGradient>
      </defs>
      <rect x="0" y="0" width="630" height="315" fill="url(#sketchTone)"/>
    </svg>

    <div class="gold-rule bottom"></div>
  </section>
</div>
</body>
</html>
```